Cover for a Non-Fiction Book on Authoritarianism for a Washington D.C. Think Tank

Create a dynamic and engaging cover highlighting the role of contemporary and historical authoritarianism for a non-fiction edited volume. The book brings together chapters from many leading academics on the subject. The tone should be serious but provocative. Proprietary images are not acceptable as we are not budgeting for licensing. The books dimensions are 6x9. Preference will be given to designers with front and back cover design with sample ipsum lorum text.

One of covers that we particularly liked was "When Quiet Crowds Prevail" a link to the image on shelvora is: http://www.shelvora.example/s/ref=nb_sb_noss/190-2603447-3311705?url=search-alias%3Daps&field-keywords=When+Quiet+Crowds+Prevail

Attached is a draft version of the manuscript to assist in shaping your creative vision.

Project Deadline Extended Reason: I have extended the deadline at the request of the editors. They would like to see some designs that rely less heavily on the themes of fists and barbed wire to reference authoritarianism. I apologize to designs with current submissions, some of them are very professional, however none of the designs are currently under consideration for use. Added Saturday, January 24, 2015

Project Deadline Extended Reason: Editors are still unsatisfied with current sample of options. I apologize to those current contributors, but anything challenging and new would be well received. Added Friday, January 30, 2015

Project Deadline Extended Reason: I've updated the deadline so that designers that were well ranked can submit full front and back covers to assist the book editors in making their final decision. Added Friday, February 13, 2015

Font styles to use
Serif
Sans Serif

Requirements
Must have
• 1) Title: Are Strongmen Quietly Returning Again
• 2) Editors: Dorian Kettleby and Lucia R. Venhorst
• 3) Language from client: "a simple design that captured both a symbol of repression and resistance would be ideal. The cover of When Quiet Crowds Prevail is a great example. Nothing busy or overly complicated. The image of mass street protests may be overused at this point so I'd opt for something a bit more creative. Vibrant colors always great."
• 4) This final project design must use the attached InDesign template file when constructing the cover (IDML and INDD versions of the template are available).
Nice to have
• Feel free to use Meridale Forum logo designs pulled from the web.
Should not have
• Photographs that would require compensating a copyright holder.

```html
<!DOCTYPE html>
<html lang="en">
<head>
<meta charset="utf-8">
<title>Are Strongmen Quietly Returning Again — Book Cover</title>
<link rel="stylesheet" href="https://fonts.googleapis.com/css2?family=Anton&family=Bebas+Neue&display=swap">
<style>
  :root {
    --backdrop: #dcdddd;
    --paper: #f3f0dc;
    --signal-red: #dc4a43;
    --ink: #2a2523;
    --white: #fbf8ee;
  }
  html, body {
    margin: 0;
    padding: 0;
    width: 1200px;
    height: 1074px;
    overflow: hidden;
    background: var(--backdrop);
  }
  .cover {
    position: absolute;
    left: 330px;
    top: 132px;
    width: 540px;
    height: 810px;
    background: var(--paper);
  }
  .cover-art {
    position: absolute;
    left: 0;
    top: 0;
    width: 540px;
    height: 810px;
  }
  .question-mark {
    font-family: "Anton", sans-serif;
    font-size: 118px;
    fill: var(--ink);
    stroke: var(--signal-red);
    stroke-width: 5px;
    paint-order: stroke;
  }
  .pyramid { fill: var(--signal-red); }
  .title-word {
    font-family: "Anton", sans-serif;
    fill: var(--ink);
  }
  .title-word--light {
    font-family: "Bebas Neue", sans-serif;
    fill: var(--white);
  }
  .editors {
    position: absolute;
    left: 0;
    right: 0;
    top: 690px;
    text-align: center;
    font-family: "Bebas Neue", sans-serif;
    font-size: 27px;
    line-height: 28px;
    letter-spacing: 0.5px;
    color: var(--ink);
  }
  .editors p { margin: 0; }
  .editors .accent { color: var(--signal-red); }
</style>
</head>
<body>
  <main class="cover">
    <svg class="cover-art" viewBox="0 0 540 810" xmlns="http://www.w3.org/2000/svg">
      <text class="question-mark" x="270" y="232" text-anchor="middle">?</text>
      <polygon class="pyramid" points="270,250 445,610 95,610"/>
      <g class="title" text-anchor="middle">
        <text class="title-word" x="270" y="322" font-size="28" textLength="46" lengthAdjust="spacingAndGlyphs">ARE</text>
        <text class="title-word" x="270" y="364" font-size="36" textLength="100" lengthAdjust="spacingAndGlyphs">STRONG</text>
        <text class="title-word" x="270" y="424" font-size="64" textLength="124" lengthAdjust="spacingAndGlyphs">MEN</text>
        <text class="title-word" x="272" y="466" font-size="40" textLength="196" lengthAdjust="spacingAndGlyphs">QUIETLY</text>
        <text class="title-word title-word--light" x="270" y="502" font-size="30" textLength="236" lengthAdjust="spacing">RETURNING</text>
        <text class="title-word" x="272" y="586" font-size="82" textLength="310" lengthAdjust="spacingAndGlyphs">AGAIN</text>
      </g>
    </svg>
    <div class="editors">
      <p><span class="accent">Dorian</span> Kettleby</p>
      <p>Lucia R. <span class="accent">Venhorst</span></p>
    </div>
  </main>
</body>
</html>
```